Manuka Honey company needs a Upmarket, Luxury Website!

New Zealand, Taranaki based Manuka Honey company Rimu Vale Honey is looking for a new website, we are looking for an upmarket, luxury, serious website design. We export the highest quality quality Manuka Honey, straight from the Taranaki region.

Main export markets are Asia & Europe, also New Zealand & Australia.

Looking to have a beautiful, upmarket, serious, luxurious & graphical experience with mobile optimization in mind. Like the use of product staging/mockups

You can use copy from other websites to build the site and we will change the copy after the design is finished.

***Please include 'Honey Product' mockups in website.

*Will add illustrator files in coming days***

Feel free to make website functional in Shopify, Wordpress or WIX

Target Market(s)

Asia, Europe (main markets) New Zealand, Australia (Submarkets)

Coding

Coded - Design and coding required

Number of Pages Required

4 page

Requirements
Must have
• Home, Shop, About Us, Contact Us

Homepage to include:

Our Products
Company Video (video under construction)
What is MGO/KPS
Newsletter Opt-in

***(Not in Order)***

Please include 'Honey Product' mockups in website.
*Will add illustrator files in coming days
Nice to have
• FAQ & Partnership Inquiries (hyperlink in footer)

```html
<!DOCTYPE html>
<html lang="en">
<head>
<meta charset="utf-8">
<title>Rimu Vale Honey</title>
<link href="https://fonts.googleapis.com/css2?family=Poppins:wght@400;500;600;700&display=swap" rel="stylesheet">
<style>
  :root{
    --ink:#1e1e1e;
    --ink-soft:#444;
    --gold:#c9a24a;
    --gold-light:#e7cf74;
    --gold-pale:#f3e69a;
    --white:#ffffff;
    --line:#e6e6e6;
    --muted:#8a8a8a;
    --placeholder-top:#eeeae0;
    --placeholder-bottom:#d9d1bd;
  }
  *{box-sizing:border-box;margin:0;padding:0}
  html,body{width:1200px;height:4448px;overflow:hidden}
  body{position:relative;background:var(--white);font-family:'Poppins',sans-serif;color:var(--ink)}
  .abs{position:absolute}

  /* hero */
  .hero-panel{left:0;top:0;width:630px;height:751px;background:var(--ink)}
  .nav{left:630px;top:0;width:570px;height:69px;background:var(--white);display:flex;align-items:center;gap:32px;padding-left:57px;font-size:13px;font-weight:500}
  .nav a{color:var(--ink);text-decoration:none}
  .nav a.active{color:var(--gold)}
  .nav-icons{display:flex;gap:10px;margin-left:4px}
  .brand{left:90px;top:21px;width:114px;height:114px;border:2px solid var(--gold);border-radius:50%;display:flex;align-items:center;justify-content:center;text-align:center;color:var(--gold);font-weight:600;font-size:13px;line-height:1.3}
  .hero-photo{left:566px;top:69px;width:634px;height:634px;background:linear-gradient(160deg,#dfe3e4 0%,#8c9272 40%,#6d6d58 70%,#8f8874 100%)}
  .hero-title{left:90px;top:322px;font-size:46px;font-weight:700;line-height:1.02;color:var(--white)}
  .hero-title span{color:var(--gold-light)}
  .hero-text{left:90px;top:428px;width:420px;font-size:14px;line-height:1.4;color:#e8e8e8}
  .btn{display:inline-flex;align-items:center;justify-content:center;background:linear-gradient(90deg,var(--gold-pale),var(--gold));color:var(--ink);font-weight:700;font-size:13px;height:32px;padding:0 18px}
  .hero-btn{left:90px;top:484px}

  /* about */
  .about-pattern{left:0;top:815px;width:371px;height:580px;background:linear-gradient(135deg,#f1f1f1,#dcdcdc)}
  .about-photo{left:88px;top:872px;width:454px;height:454px;background:linear-gradient(180deg,#7ea3d6 0%,#c9d6e4 35%,#4e6a37 60%,#6f8b48 100%);box-shadow:0 30px 40px rgba(0,0,0,.15)}
  .h2{font-size:40px;font-weight:500;line-height:1;letter-spacing:.5px}
  .h2.bold{font-weight:700}
  .h2 span{color:var(--gold-light)}
  .rule{width:48px;height:3px;background:var(--gold)}
  .body{font-size:15px;line-height:1.6;color:var(--ink-soft);white-space:nowrap}
  .about-h{left:601px;top:1002px}
  .about-rule{left:601px;top:1050px}
  .about-text{left:601px;top:1066px}
  .about-btn{left:601px;top:1228px}

  /* products */
  .products{left:0;top:1440px;width:1200px;height:589px;background:linear-gradient(120deg,#f8efa0 0%,#ead27e 45%,#d4b060 100%)}
  .products-h{left:0;top:1543px;width:1200px;text-align:center}
  .products-rule{left:576px;top:1592px}
  .card{top:1675px;width:247px;height:271px;background:var(--white);box-shadow:0 6px 18px rgba(0,0,0,.08);text-align:center}
  .product-shot{position:absolute;left:50%;top:-35px;transform:translateX(-50%);width:160px;height:185px;background:linear-gradient(180deg,var(--placeholder-top),var(--placeholder-bottom))}
  .card-name{position:absolute;left:0;right:0;top:180px;font-size:15px;font-weight:600}
  .stars{position:absolute;left:0;right:0;top:204px;color:var(--gold-light);font-size:13px;letter-spacing:3px}
  .price{position:absolute;left:0;right:0;top:222px;font-size:19px;font-weight:700;color:var(--gold)}

  /* mgo */
  .mgo-h{left:90px;top:2186px}
  .mgo-rule{left:90px;top:2232px}
  .mgo-text{left:90px;top:2248px}
  .mgo-list{left:90px;top:2355px;list-style:none;font-size:15px;line-height:26.5px;color:var(--ink)}
  .mgo-btn{left:90px;top:2495px}
  .mgo-photo{left:658px;top:2029px;width:542px;height:570px;background:radial-gradient(circle at 55% 65%,#d89b2c 0%,#8a5a1a 30%,#2b2722 60%,#1a1a1a 100%);box-shadow:0 20px 40px rgba(0,0,0,.12)}

  /* video */
  .video{left:90px;top:2687px;width:1020px;height:487px;background:linear-gradient(110deg,#6fa6d8 0%,#d6dee6 35%,#c08a2a 55%,#4a6c8e 100%)}
  .play{left:213px;top:2917px;width:86px;height:86px;border:3px solid var(--white);border-radius:50%}
  .video-title{left:639px;top:2912px;font-size:42px;font-weight:500;line-height:1.08;color:var(--white)}

  /* review */
  .quote{left:540px;top:3245px;width:120px;height:90px}
  .review-h{left:0;top:3318px;width:1200px;text-align:center}
  .review-rule{left:576px;top:3368px}
  .review-text{left:0;top:3390px;width:1200px;text-align:center;font-size:15px;line-height:1.55;color:var(--ink-soft)}
  .review-name{left:0;top:3473px;width:1200px;text-align:center;font-size:15px;font-weight:700}
  .review-role{left:0;top:3495px;width:1200px;text-align:center;font-size:13px;color:var(--ink-soft)}
  .dots{left:582px;top:3536px;display:flex;gap:6px}
  .dots i{width:8px;height:8px;border-radius:50%;background:#bbb}
  .dots i:first-child{background:var(--gold)}
  .divider{left:90px;top:3600px;width:1020px;height:1px;background:var(--line)}

  /* partners */
  .partner-h{left:0;top:3690px;width:1200px;text-align:center}
  .partner-rule{left:576px;top:3738px}
  .partners{left:90px;top:3765px;display:flex;gap:10px}
  .partner{width:196px;height:76px;border:1px solid var(--line);display:flex;align-items:center;justify-content:center}
  .partner i{width:110px;height:22px;background:#d6d6d6;border-radius:11px}

  /* footer */
  .footer{left:0;top:4010px;width:1200px;height:438px;background:var(--ink)}
  .newsletter{left:90px;top:3912px;width:1110px;height:160px;background:linear-gradient(90deg,#f6eea6 0%,#e9d07d 50%,#c9a24a 100%)}
  .news-title{left:155px;top:3958px;font-size:33px;font-weight:700;line-height:1.05;color:var(--ink)}
  .news-input{left:587px;top:3974px;width:387px;height:43px;background:var(--white);font-size:13px;color:var(--ink-soft);display:flex;align-items:center;padding-left:20px}
  .news-btn{left:974px;top:3974px;width:136px;height:43px;background:var(--ink);color:var(--white);font-size:14px;font-weight:600;display:flex;align-items:center;justify-content:center}
  .foot-brand{left:101px;top:4181px;width:144px;height:144px;border:2px solid var(--gold);border-radius:50%;display:flex;align-items:center;justify-content:center;text-align:center;color:var(--gold);font-weight:600;font-size:16px;line-height:1.3}
  .foot-col{top:4196px}
  .foot-col h4{font-size:18px;font-weight:600;color:var(--gold-light);margin-bottom:6px}
  .foot-col a{display:block;font-size:13.5px;line-height:28.5px;color:#cfcfcf;text-decoration:none}
  .social{top:4236px;left:938px;display:flex;gap:8px}
  .social i{width:34px;height:34px;border:1px solid #777;border-radius:50%}
  .to-top{left:1125px;top:4374px;width:36px;height:36px;border-radius:50%;background:var(--gold-light);display:flex;align-items:center;justify-content:center}
  .copy{left:0;top:4413px;width:1200px;text-align:center;font-size:13.5px;color:var(--gold-light)}
</style>
</head>
<body>

<!-- hero -->
<div class="abs hero-panel"></div>
<div class="abs brand">Rimu Vale<br>Honey</div>
<nav class="abs nav">
  <a class="active" href="#">HOME</a>
  <a href="#">SHOP</a>
  <a href="#">ABOUT US</a>
  <a href="#">CONTACT US</a>
  <span class="nav-icons">
    <svg width="16" height="16" viewBox="0 0 16 16"><circle cx="6.5" cy="6.5" r="5" fill="none" stroke="#1e1e1e" stroke-width="2"/><path d="M10 10l5 5" stroke="#1e1e1e" stroke-width="2"/></svg>
    <svg width="16" height="16" viewBox="0 0 16 16"><circle cx="8" cy="5" r="3.5" fill="none" stroke="#1e1e1e" stroke-width="1.5"/><path d="M1.5 15c1-4 12-4 13 0" fill="none" stroke="#1e1e1e" stroke-width="1.5"/></svg>
    <svg width="20" height="18" viewBox="0 0 20 18"><path d="M2 6h12l-1 11H3z" fill="none" stroke="#1e1e1e" stroke-width="1.5"/><path d="M5 6V4a3 3 0 016 0v2" fill="none" stroke="#1e1e1e" stroke-width="1.5"/><circle cx="16" cy="3" r="3" fill="#c9a24a"/></svg>
  </span>
</nav>
<div class="abs hero-photo" role="img" aria-label="Beekeepers in protective suits walking beside hives on a hillside"></div>
<h1 class="abs hero-title">WELCOME<br><span>RIMU VALE HONEY</span></h1>
<p class="abs hero-text">We export the highest quality quality Manuka Honey, straight from the Taranaki region.</p>
<a class="abs btn hero-btn">SHOP NOW</a>

<!-- about -->
<div class="abs about-pattern" role="img" aria-label="Soft grey decorative koru background"></div>
<div class="abs about-photo" role="img" aria-label="Beekeepers tending hives in a sunlit green valley"></div>
<h2 class="abs h2 bold about-h">ABOUT <span>US</span></h2>
<div class="abs rule about-rule"></div>
<p class="abs body about-text">Lorem Ipsum is simply dummy text of the printing and typesetting<br>industry. Lorem Ipsum has been the industry's standard dummy text<br>ever since the 1500s, when an unknown printer took a galley of type<br>and scrambled it to make a type specimen book. It has survived not<br>only five centuries, but also the leap into electronic typesetting,<br>remaining essentially unchanged.</p>
<a class="abs btn about-btn">READ MORE</a>

<!-- products -->
<section class="abs products" role="img" aria-label="Golden gradient background with faint decorative pattern"></section>
<h2 class="abs h2 products-h">OUR PRODUCTS</h2>
<div class="abs rule products-rule"></div>
<div class="abs card" style="left:90px"><div class="product-shot" role="img" aria-label="Product photo of a manuka honey jar"></div><div class="card-name">Products Heading here</div><div class="stars">★★★★★</div><div class="price">$25.00</div></div>
<div class="abs card" style="left:347px"><div class="product-shot" role="img" aria-label="Product photo of a manuka honey jar"></div><div class="card-name">Products Heading here</div><div class="stars">★★★★★</div><div class="price">$25.00</div></div>
<div class="abs card" style="left:606px"><div class="product-shot" role="img" aria-label="Product photo of a manuka honey jar"></div><div class="card-name">Products Heading here</div><div class="stars">★★★★★</div><div class="price">$25.00</div></div>
<div class="abs card" style="left:864px"><div class="product-shot" role="img" aria-label="Product photo of a manuka honey jar"></div><div class="card-name">Products Heading here</div><div class="stars">★★★★★</div><div class="price">$25.00</div></div>

<!-- mgo -->
<h2 class="abs h2 mgo-h">WHAT IS <span>MGO/KPS</span></h2>
<div class="abs rule mgo-rule"></div>
<p class="abs body mgo-text">Lorem Ipsum is simply dummy text of the printing and typesetting<br>industry. Lorem Ipsum has been the industry's standard dummy text<br>ever since the 1500s, when an unknown printer took a galley of type<br>and scrambled it to make a type specimen book.</p>
<ul class="abs mgo-list">
  <li>KPS 5 = MGO83</li>
  <li>KPS10 = MGO263</li>
  <li>KPS15 = MGO514</li>
  <li>KPS20 = MGO829</li>
  <li>KPS25 = MGO1200</li>
</ul>
<a class="abs btn mgo-btn">READ MORE</a>
<div class="abs mgo-photo" role="img" aria-label="Jars of honey with a wooden dipper and honeycomb on a dark background"></div>

<!-- video -->
<div class="abs video" role="img" aria-label="Beekeeper holding a honeycomb frame surrounded by bees"></div>
<div class="abs play"><svg width="80" height="80" viewBox="0 0 80 80"><path d="M32 26l22 14-22 14z" fill="#fff"/></svg></div>
<h2 class="abs video-title">UNLOCKING<br>NATURE'S SECRETS</h2>

<!-- review -->
<svg class="abs quote" viewBox="0 0 120 90"><path d="M8 85V50Q8 15 45 5v14Q28 26 28 45h18v40zM68 85V50Q68 15 105 5v14Q88 26 88 45h18v40z" fill="#ececec"/></svg>
<h2 class="abs h2 review-h">CUSTOMER <span>REVIEW</span></h2>
<div class="abs rule review-rule"></div>
<p class="abs review-text">Lorem Ipsum is simply dummy text of the printing and typesetting<br>industry.Lorem Ipsum has been the industry's standard dummy text ever since<br>the when an unknown printer .</p>
<div class="abs review-name">JOHN SMITH</div>
<div class="abs review-role">Co founder</div>
<div class="abs dots"><i></i><i></i><i></i></div>
<div class="abs divider"></div>

<!-- partners -->
<h2 class="abs h2 partner-h">OUR <span>PARTNER</span></h2>
<div class="abs rule partner-rule"></div>
<div class="abs partners">
  <div class="partner"><i></i></div>
  <div class="partner"><i></i></div>
  <div class="partner"><i></i></div>
  <div class="partner"><i></i></div>
  <div class="partner"><i></i></div>
</div>

<!-- footer -->
<footer class="abs footer"></footer>
<div class="abs newsletter"></div>
<h3 class="abs news-title">SUBSCRIBE TO<br>OUR NEWSLETTER</h3>
<div class="abs news-input">Enter your email</div>
<div class="abs news-btn">SUBSCRIBE</div>
<div class="abs foot-brand">Rimu Vale<br>Honey</div>
<div class="abs foot-col" style="left:328px"><h4>WHO WE ARE</h4><a>About Us</a><a>FAQ</a><a>Partnership Inquiries</a></div>
<div class="abs foot-col" style="left:565px"><h4>LET US HELP</h4><a>Shipping</a><a>FAQ</a><a>My Account</a></div>
<div class="abs foot-col" style="left:753px"><h4>EXPLORE</h4><a>Ingredients</a><a>Blog</a><a>Privacy Policy</a></div>
<div class="abs social"><i></i><i></i><i></i><i></i></div>
<div class="abs to-top"><svg width="14" height="10" viewBox="0 0 14 10"><path d="M1 8l6-6 6 6" fill="none" stroke="#1e1e1e" stroke-width="2"/></svg></div>
<div class="abs copy">Copyright 2021 | All Rights Reserved</div>

</body>
</html>
```